Business card design needed

I would like a one sided black business card with the information provided above. Refer to my website www.brightvolleyracquets.com.au for an example of colors I have used for my site, would like to keep this consistent for my business cards also, I will upload my logo below.

I am a new small business that provides tennis customers with racquet re stringing, tennis strings and accessories.

Industry/Entity Type

Small Business

Contact Information for Business Card

Bright Volley Tennis

Owen Whitby
Managing Director

brightvolleyracquets@mailbox.example
www.brightvolleyracquets.com.au
0491 726 305

Racquet Restringing/Tennis Strings/Accessories

Requirements
Must have
• Must have my logo and card must be black

```html
<!DOCTYPE html>
<html lang="en">
<head>
<meta charset="utf-8">
<title>Bright Volley Tennis – Business Card</title>
<link rel="stylesheet" href="https://fonts.googleapis.com/css2?family=Open+Sans:wght@400;600;700&display=swap">
<style>
  :root {
    --page: #e9e6e1;
    --card: #000000;
    --ink: #ffffff;
    --lime: #bdd63f;
    --lime-band: #c0d84c;
    --blue-band: #3e6698;
    --dark-ink: #111111;
  }
  html, body {
    margin: 0;
    padding: 0;
    width: 1200px;
    height: 750px;
    overflow: hidden;
    background: var(--page);
  }
  .canvas {
    position: relative;
    width: 1200px;
    height: 750px;
    font-family: "Open Sans", sans-serif;
  }
  .card {
    position: absolute;
    left: 75px;
    top: 75px;
    width: 1050px;
    height: 597px;
    border-radius: 40px;
    background: var(--card);
    overflow: hidden;
    color: var(--ink);
  }
  .brand {
    position: absolute;
    left: 0;
    right: 0;
    top: 118px;
    display: flex;
    justify-content: center;
    align-items: center;
    gap: 16px;
  }
  .brand-dot {
    width: 34px;
    height: 34px;
    border-radius: 50%;
    background: var(--lime);
  }
  .brand-name {
    font-size: 46px;
    font-weight: 700;
    color: var(--lime);
    letter-spacing: 0.5px;
  }
  .services {
    position: absolute;
    left: 57px;
    top: 268px;
    margin: 0;
    padding: 0;
    list-style: none;
    font-size: 30px;
    line-height: 40px;
  }
  .services li::before {
    content: "";
    display: inline-block;
    width: 9px;
    height: 9px;
    background: var(--ink);
    margin-right: 10px;
    vertical-align: 7px;
  }
  .contact {
    position: absolute;
    left: 636px;
    top: 290px;
  }
  .contact-name {
    font-size: 32px;
    font-weight: 700;
    color: var(--lime);
    line-height: 44px;
  }
  .contact-role {
    font-size: 26px;
    line-height: 34px;
  }
  .contact-phone {
    margin-top: 12px;
    font-size: 27px;
    display: flex;
    align-items: center;
    gap: 16px;
  }
  .bands {
    position: absolute;
    left: 0;
    top: 0;
  }
  .email {
    position: absolute;
    left: 78px;
    top: 455px;
    font-size: 24px;
  }
  .website {
    position: absolute;
    left: 643px;
    top: 491px;
    font-size: 24px;
    color: var(--dark-ink);
  }
</style>
</head>
<body>
<div class="canvas">
  <div class="card">
    <svg class="bands" width="1050" height="597" viewBox="0 0 1050 597" aria-hidden="true">
      <polygon points="483,473 1050,473 1050,543 483,543 545,473" fill="var(--lime-band)"/>
      <polygon points="0,438 613,438 547,508 0,508" fill="var(--blue-band)"/>
    </svg>

    <div class="brand">
      <span class="brand-dot"></span>
      <span class="brand-name">Bright Volley Tennis</span>
    </div>

    <ul class="services">
      <li>Racquet Restringing</li>
      <li>Tennis Strings</li>
      <li>Accessories</li>
    </ul>

    <div class="contact">
      <div class="contact-name">Owen Whitby</div>
      <div class="contact-role">Managing Director</div>
      <div class="contact-phone">
        <svg width="20" height="16" viewBox="0 0 20 16" aria-hidden="true">
          <path d="M1 5 C1 1 19 1 19 5 L19 7 L15 7 L14 4 L6 4 L5 7 L1 7 Z" fill="var(--lime)"/>
          <path d="M6 6 L14 6 L18 15 L2 15 Z" fill="var(--lime)"/>
          <circle cx="10" cy="10.5" r="2" fill="var(--card)"/>
        </svg>
        <span>0491 726 305</span>
      </div>
    </div>

    <div class="email">brightvolleyracquets@mailbox.example</div>
    <div class="website">www.brightvolleyracquets.com.au</div>
  </div>
</div>
</body>
</html>
```